Landing Page and Logo for Auto-Blogging Platform

I created a platform that allows users to start a blog for their business, hobby, charity, etc. I need a landing page where users can learn about the platform, benefits of consistent blogging, SEO value, plans/pricing, etc. The landing page needs to have multiple call to action buttons encouraging the visitor to register/sign up for a free trial.

In addition to the landing page, I need a page for users to establish the settings for their blog. This page should be a fairly simple form, intended for the user to enter a few details to set up their blog:
1. Name of Blog
2. Up to 10 topics and/or keywords the blog should focus on
3. Theme: Color-scheme and logo upload for blog.

I have attached the specifications of the platform's functionality so you can better understand how it works, plans/pricing, etc.

I also need a logo for the business. The name of the platform is PostNook.

Target Market(s)

Website owners, bloggers, business owners

Industry/Entity Type

Technology, Internet, web design

Coding

Coded - Design and coding required

Number of Pages Required

2 page

Colors
0054AA
0677BA
7BADD7
CADEEF
E8F1F8
0094D4
00A9DD
6FCCEA
C7EBF8
E9F6FB

Requirements
Must have
• Eye-catching design but fairly light on content (keep it simple and brief.)
Nice to have
• Eye-catching yet simple design, clean and easy to understand what we are offering.
Should not have
• Too much “wordy” and confusing content.

```html
<!DOCTYPE html>
<html lang="en">
<head>
<meta charset="utf-8">
<title>PostNook – Auto-Blogging Platform</title>
<link rel="stylesheet" href="https://fonts.googleapis.com/css2?family=Lato:wght@300;400;700;900&display=swap">
<style>
:root{
  --blue:#0054AA;
  --blue-mid:#0677BA;
  --blue-soft:#7BADD7;
  --blue-pale:#CADEEF;
  --blue-mist:#E8F1F8;
  --ink:#111418;
  --text:#2a2d33;
  --muted:#4a4f57;
  --white:#ffffff;
  --footer:#f3f5f8;
}
*{box-sizing:border-box;margin:0;padding:0}
html,body{width:1200px;height:3490px;overflow:hidden}
body{position:relative;font-family:"Lato",sans-serif;color:var(--text);background:var(--white)}
.abs{position:absolute}
.btn{position:absolute;display:flex;align-items:center;justify-content:center;gap:10px;background:var(--blue);color:var(--white);font-weight:700;font-size:16px;border-radius:5px;text-decoration:none}
.logo-word{font-weight:900;color:var(--ink);letter-spacing:-.5px}

/* hero */
.hero-bg{left:0;top:0;width:1200px;height:1040px;background:linear-gradient(180deg,var(--blue-mist) 0%,#f3f8fc 55%,var(--white) 100%)}
.brand{left:111px;top:24px;font-size:38px}
.nav{left:446px;top:36px;display:flex;gap:0;font-size:17px;color:var(--ink)}
.nav a{color:var(--ink);text-decoration:none;position:absolute;white-space:nowrap}
.nav .active{color:var(--blue);font-weight:700;border-bottom:2px solid var(--blue);padding-bottom:2px}
.register{left:952px;top:26px;width:135px;height:46px}
.eyebrow{left:0;width:1200px;top:154px;text-align:center;font-weight:700;font-size:20px;color:var(--ink)}
.hero-title{left:0;width:1200px;top:178px;text-align:center;font-size:96px;line-height:1.1}
.hero-lead{left:270px;width:660px;top:300px;text-align:center;font-size:17px;line-height:31px;color:var(--ink)}
.trial{left:494px;top:380px;width:211px;height:51px;font-size:16px}
.device{left:261px;top:497px;width:677px;height:516px;border-radius:26px;background:#1d1f24;padding:18px}
.device .screen{width:100%;height:100%;border-radius:10px;background:linear-gradient(135deg,#f2f2f2 0%,#dfe6ee 45%,#f5b6c8 60%,#e9eef3 100%)}

/* methods */
.section-title{left:0;width:1200px;text-align:center;font-size:40px;font-weight:400;color:var(--ink)}
.section-title strong{color:var(--blue);font-weight:700}
.method{width:301px;height:151px;background:var(--white);box-shadow:0 4px 22px rgba(0,40,90,.1);border-radius:3px;text-align:center;font-size:18px;line-height:31px;color:var(--ink);padding:58px 18px 0}
.method-icon{width:68px;height:68px;border-radius:50%;background:var(--blue);border:5px solid var(--white);box-shadow:0 3px 12px rgba(0,40,90,.2);display:flex;align-items:center;justify-content:center}

/* about */
.about-photo{left:0;top:1432px;width:601px;height:502px;background:linear-gradient(120deg,#d9d1c6 0%,#bfae98 45%,#8a7560 100%)}
.about-panel{left:601px;top:1432px;width:599px;height:502px;background:var(--blue);color:var(--white)}
.about-title{left:663px;top:1492px;font-size:40px;font-weight:400;color:var(--white)}
.about-title strong{font-weight:900}
.about-copy{left:663px;top:1554px;width:426px;font-size:15px;line-height:25.5px;text-align:justify;color:var(--white)}
.about-copy p+p{margin-top:17px}
.read-more{left:665px;top:1809px;width:143px;height:50px;background:var(--white);color:var(--blue)}

/* pricing */
.plan{background:var(--white);box-shadow:0 4px 24px rgba(0,40,90,.1);text-align:center;color:var(--ink)}
.plan h3{font-size:21px;font-weight:400;margin-bottom:20px}
.plan .desc{font-size:16px;line-height:29px}
.price{font-size:46px;font-weight:700;margin:14px 0 16px}
.price span{font-size:12px;font-weight:400;color:var(--muted)}
.features{list-style:none;text-align:left;display:inline-block;font-size:13.5px;color:var(--muted)}
.features li{display:flex;align-items:center;gap:10px;height:29px}
.features svg{flex:none}
.plan .btn{position:relative;margin:20px auto 0;width:133px;height:46px;font-size:15px}
.plan.featured{border-bottom:4px solid var(--blue)}
.plan.featured h3{color:var(--blue);font-weight:700;font-size:24px}

/* benefits */
.benefits{left:111px;top:2731px;list-style:none;font-size:17px;color:var(--ink)}
.benefits li{display:flex;align-items:center;gap:12px;height:42.8px}
.benefit-photo{left:655px;top:2739px;width:432px;height:314px;border:3px solid var(--blue);border-radius:14px;background:linear-gradient(135deg,#c9d3dc 0%,#a9825a 50%,#6b4a30 100%)}
.view-more{left:111px;top:3002px;width:142px;height:51px}

/* footer */
.footer{left:0;top:3144px;width:1200px;height:346px;background:var(--footer)}
.footer-brand{left:0;width:1200px;top:3192px;text-align:center;font-size:48px}
.footer-nav{left:0;width:1200px;top:3282px;display:flex;justify-content:center;gap:48px;font-size:18px;color:var(--ink)}
.copyright{left:0;width:1200px;top:3340px;text-align:center;font-size:15px;font-weight:700;color:var(--ink)}
.payments{left:0;width:1200px;top:3400px;display:flex;justify-content:center;gap:44px;font-size:22px;font-weight:700;color:#3d4a66}
</style>
</head>
<body>

<div class="abs hero-bg"></div>

<header>
  <div class="abs brand logo-word">PostNook</div>
  <nav class="abs nav">
    <a class="active" style="left:0">Home</a>
    <a style="left:92px">About the platform</a>
    <a style="left:285px">Benefits</a>
    <a style="left:394px">Pricing</a>
  </nav>
  <a class="btn register">Register
    <svg width="20" height="20" viewBox="0 0 20 20" fill="none" stroke="#fff" stroke-width="1.8"><path d="M4 2h9v6M4 2v16h6M7 7h5M7 11h3"/><path d="M11 17l1-3 5-5 2 2-5 5z"/></svg>
  </a>
</header>

<section>
  <div class="abs eyebrow">WELCOME TO</div>
  <h1 class="abs hero-title logo-word">PostNook</h1>
  <p class="abs hero-lead">There needs to be a super-admin panel where platform owner/administrator can see users, their activity, manage user access, etc.</p>
  <a class="btn trial">Sign up for a free trial</a>
  <div class="abs device"><div class="screen" role="img" aria-label="Tablet showing a sample news blog homepage with articles and photos"></div></div>
</section>

<section>
  <h2 class="abs section-title" style="top:1070px">The blog <strong>Using These Methods</strong></h2>

  <div class="abs method" style="left:111px;top:1192px">The user enters them into a table manually.</div>
  <div class="abs method" style="left:450px;top:1192px">The user uploads a list of blog topics in CSV format.</div>
  <div class="abs method" style="left:787px;top:1192px">Provide a list of 52 blog topics for a handyman business's blog.</div>

  <div class="abs method-icon" style="left:228px;top:1160px">
    <svg width="34" height="34" viewBox="0 0 24 24" fill="none" stroke="#fff" stroke-width="1.4"><circle cx="12" cy="12" r="3.2"/><path d="M12 2.5v3M12 18.5v3M2.5 12h3M18.5 12h3M5.3 5.3l2.1 2.1M16.6 16.6l2.1 2.1M5.3 18.7l2.1-2.1M16.6 7.4l2.1-2.1"/><circle cx="12" cy="12" r="6.5"/></svg>
  </div>
  <div class="abs method-icon" style="left:566px;top:1160px">
    <svg width="32" height="32" viewBox="0 0 24 24" fill="none" stroke="#fff" stroke-width="1.4"><path d="M6 2h8l4 4v9M6 2v18h7"/><path d="M9 8h6M9 11h5"/><circle cx="17" cy="18" r="4"/><path d="M17 20v-4M15.5 17.5 17 16l1.5 1.5"/></svg>
  </div>
  <div class="abs method-icon" style="left:904px;top:1160px">
    <svg width="32" height="32" viewBox="0 0 24 24" fill="none" stroke="#fff" stroke-width="1.4"><rect x="3" y="5" width="15" height="12" rx="1"/><path d="M6 9h7M6 12h5M8 17l-2 3M13 17l2 3"/><path d="M15 10l6-6 1 1-6 6-2 1z"/></svg>
  </div>
</section>

<section>
  <div class="abs about-photo" role="img" aria-label="Photo of a smiling woman in glasses reading on a tablet in a bright office"></div>
  <div class="abs about-panel"></div>
  <h2 class="abs about-title">About <strong>PostNook</strong></h2>
  <div class="abs about-copy">
    <p>The platform will require a list of blog topics. Based on the topics list, the software will need to automatically send prompts to TextMind in the specified intervals (monthly, weekly, or daily), receive the blog content, and post it to the blog.</p>
    <p>Furthermore, the software will need some method of adding at least one image to each blog post. Ideally, this would be achieved by using the PixStock API to retrieve image(s) based on keywords in the blog topic.</p>
  </div>
  <a class="btn read-more">Read More</a>
</section>

<section>
  <h2 class="abs section-title" style="top:1985px">Our <strong style="color:var(--ink)">Pricing</strong> <strong>Plans</strong></h2>

  <div class="abs plan" style="left:165px;top:2095px;width:286px;height:453px;padding-top:52px">
    <h3>Base Plan</h3>
    <p class="desc">1 blog post<br>(up to 2,000 words)</p>
    <div class="price">$9.99<span>/month</span></div>
    <ul class="features">
      <li><svg width="12" height="10" viewBox="0 0 12 10"><path d="M1 5l3.5 3.5L11 1.5" fill="none" stroke="#2a2d33" stroke-width="2"/></svg>Reprehenderit in voluptate</li>
      <li><svg width="12" height="10" viewBox="0 0 12 10"><path d="M1 5l3.5 3.5L11 1.5" fill="none" stroke="#2a2d33" stroke-width="2"/></svg>Velit esse cillum dolore eu</li>
      <li><svg width="12" height="10" viewBox="0 0 12 10"><path d="M1 5l3.5 3.5L11 1.5" fill="none" stroke="#2a2d33" stroke-width="2"/></svg>Fugiat nulla pariatur</li>
      <li><svg width="12" height="10" viewBox="0 0 12 10"><path d="M1 5l3.5 3.5L11 1.5" fill="none" stroke="#2a2d33" stroke-width="2"/></svg>Mollit anim id est laborum</li>
    </ul>
    <a class="btn">Buy Now</a>
  </div>

  <div class="abs plan" style="left:750px;top:2095px;width:286px;height:453px;padding-top:52px">
    <h3 style="margin-bottom:10px">Ultimate Plan</h3>
    <p class="desc">1 blog post<br>(up to 3,000 words)<br><span style="font-weight:700">per day plus unlimited manual</span></p>
    <div class="price" style="margin-top:8px">$24.99<span>/month</span></div>
    <ul class="features">
      <li><svg width="12" height="10" viewBox="0 0 12 10"><path d="M1 5l3.5 3.5L11 1.5" fill="none" stroke="#2a2d33" stroke-width="2"/></svg>Reprehenderit in voluptate</li>
      <li><svg width="12" height="10" viewBox="0 0 12 10"><path d="M1 5l3.5 3.5L11 1.5" fill="none" stroke="#2a2d33" stroke-width="2"/></svg>Velit esse cillum dolore eu</li>
      <li><svg width="12" height="10" viewBox="0 0 12 10"><path d="M1 5l3.5 3.5L11 1.5" fill="none" stroke="#2a2d33" stroke-width="2"/></svg>Fugiat nulla pariatur</li>
      <li><svg width="12" height="10" viewBox="0 0 12 10"><path d="M1 5l3.5 3.5L11 1.5" fill="none" stroke="#2a2d33" stroke-width="2"/></svg>Mollit anim id est laborum</li>
    </ul>
    <a class="btn" style="margin-top:14px">Buy Now</a>
  </div>

  <div class="abs plan featured" style="left:451px;top:2072px;width:299px;height:497px;padding-top:36px;box-shadow:0 6px 30px rgba(0,40,90,.16)">
    <h3 style="margin-bottom:16px">Premium Plan</h3>
    <p class="desc">1 blog post<br>(up to 2,000 words) every week</p>
    <div class="price">$14.99<span>/month</span></div>
    <ul class="features" style="font-size:14px">
      <li style="height:32.5px"><svg width="12" height="10" viewBox="0 0 12 10"><path d="M1 5l3.5 3.5L11 1.5" fill="none" stroke="#0054AA" stroke-width="2"/></svg>Duis aute irure dolor in</li>
      <li style="height:32.5px"><svg width="12" height="10" viewBox="0 0 12 10"><path d="M1 5l3.5 3.5L11 1.5" fill="none" stroke="#0054AA" stroke-width="2"/></svg>Reprehenderit in voluptate</li>
      <li style="height:32.5px"><svg width="12" height="10" viewBox="0 0 12 10"><path d="M1 5l3.5 3.5L11 1.5" fill="none" stroke="#0054AA" stroke-width="2"/></svg>Velit esse cillum dolore eu</li>
      <li style="height:32.5px"><svg width="12" height="10" viewBox="0 0 12 10"><path d="M1 5l3.5 3.5L11 1.5" fill="none" stroke="#0054AA" stroke-width="2"/></svg>Fugiat nulla pariatur</li>
      <li style="height:32.5px"><svg width="12" height="10" viewBox="0 0 12 10"><path d="M1 5l3.5 3.5L11 1.5" fill="none" stroke="#0054AA" stroke-width="2"/></svg>Mollit anim id est laborum</li>
    </ul>
    <a class="btn" style="width:151px;margin-top:30px">Buy Now</a>
  </div>
</section>

<section>
  <h2 class="abs section-title" style="top:2648px">Our <strong>Benefits</strong></h2>
  <ul class="abs benefits">
    <li><svg width="14" height="11" viewBox="0 0 12 10"><path d="M1 5l3.5 3.5L11 1.5" fill="none" stroke="#0054AA" stroke-width="2.2"/></svg>Ut enim ad minim veniam, quis nostrud exercitation ullamco</li>
    <li><svg width="14" height="11" viewBox="0 0 12 10"><path d="M1 5l3.5 3.5L11 1.5" fill="none" stroke="#0054AA" stroke-width="2.2"/></svg>Laboris nisi ut aliquip ex ea commodo consequat</li>
    <li><svg width="14" height="11" viewBox="0 0 12 10"><path d="M1 5l3.5 3.5L11 1.5" fill="none" stroke="#0054AA" stroke-width="2.2"/></svg>Duis aute irure dolor in reprehenderit in voluptate velit esse</li>
    <li><svg width="14" height="11" viewBox="0 0 12 10"><path d="M1 5l3.5 3.5L11 1.5" fill="none" stroke="#0054AA" stroke-width="2.2"/></svg>Cillum dolore eu fugiat nulla pariatur ad minim veniam</li>
    <li><svg width="14" height="11" viewBox="0 0 12 10"><path d="M1 5l3.5 3.5L11 1.5" fill="none" stroke="#0054AA" stroke-width="2.2"/></svg>Lorem ipsum dolor sit amet, consectetur adipiscing elit, sed</li>
    <li><svg width="14" height="11" viewBox="0 0 12 10"><path d="M1 5l3.5 3.5L11 1.5" fill="none" stroke="#0054AA" stroke-width="2.2"/></svg>Tempor incididunt ut labore et dolore magna aliqua.</li>
  </ul>
  <a class="btn view-more">View More</a>
  <div class="abs benefit-photo" role="img" aria-label="Overhead photo of a person working on a laptop at a wooden desk with a coffee mug"></div>
</section>

<footer>
  <div class="abs footer"></div>
  <div class="abs footer-brand logo-word">PostNook</div>
  <nav class="abs footer-nav"><span>Home</span><span>About the platform</span><span>Benefits</span><span>Pricing</span><span>Contact Us</span></nav>
  <p class="abs copyright">Copyrights@2024.PostNook.All Rights Reserved</p>
  <div class="abs payments"><span>PayStream</span><span>CoinPal</span><span>TapWallet</span><span>SwiftPay</span><span>CartPay</span></div>
</footer>

</body>
</html>
```